Young, dynamic furniture company needs a new business card design

We require a new business card design for our modern furniture company which supplies furniture and appliances to the property and development market.
Oakridge Interiors has become one of the leading furniture & appliance suppliers to the property market withing London. With over 10 years experience, we have increased our business to supply not only private landlords and managing agents, but also property developers, housing associations and local councils.
We offer not only a complete range of furniture which includes beds, wardrobes, dining sets and sofas, but also a high quality, full delivery and assembly service to help you with all our furnishing needs.

Target Market(s)

Private landlords, estate agents, letting agents, property management companies

Industry/Entity Type

Business

Contact Information for Business Card

Name,
Title,
Address,
Mobile,
Telephone,
Fax, Website, email address

Font styles to use
Sans Serif

Colors
3176b5
0555a3
85abd2
cfdeed

Requirements
Must have
• All the above information for each of our staff, along with our logo

```html
<!DOCTYPE html>
<html lang="en">
<head>
<meta charset="utf-8">
<title>Oakridge Interiors – Business Card</title>
<link href="https://fonts.googleapis.com/css2?family=Roboto:wght@300;400;700;900&display=swap" rel="stylesheet">
<style>
  :root {
    --stage: #1c1c1e;
    --card: #ffffff;
    --ink: #2f2f33;
    --ink-soft: #55565b;
    --blue: #3176b5;
    --blue-deep: #0555a3;
    --blue-mid: #85abd2;
    --blue-pale: #cfdeed;
    --charcoal: #1f1d1f;
  }
  * { margin: 0; padding: 0; box-sizing: border-box; }
  html, body {
    width: 1200px; height: 923px; overflow: hidden;
    background: var(--stage);
    font-family: "Roboto", sans-serif;
  }
  .stage {
    width: 1200px; height: 923px;
    display: flex; align-items: center; justify-content: center; gap: 48px;
  }
  .card {
    position: relative;
    width: 540px; height: 309px;
    background: var(--card);
    border-radius: 22px;
    overflow: hidden;
    box-shadow: 0 18px 40px rgba(0,0,0,.45);
  }

  /* brand lockup */
  .brand { display: flex; align-items: center; gap: 12px; }
  .brand-square { width: 30px; height: 30px; background: var(--blue); flex: none; }
  .brand-name {
    font-weight: 400; font-size: 26px; letter-spacing: .5px;
    color: var(--blue-deep); text-transform: uppercase; white-space: nowrap;
  }
  .brand-tagline {
    font-weight: 300; font-size: 11px; letter-spacing: .6px;
    color: var(--ink-soft); text-transform: uppercase; margin-top: 4px;
  }

  /* logo side */
  .card--logo { display: flex; flex-direction: column; align-items: center; justify-content: center; }
  .card--logo .brand-tagline { text-align: center; padding-left: 42px; }
  .card--logo .site { margin-top: 34px; font-size: 15px; color: var(--ink); }

  /* contact side */
  .card--contact .lockup { position: absolute; left: 28px; top: 26px; }
  .card--contact .brand-name { font-size: 21px; }
  .card--contact .brand-square { width: 24px; height: 24px; }
  .card--contact .brand-tagline { font-size: 9.5px; padding-left: 36px; }
  .watermark {
    position: absolute; left: 40px; top: 96px;
    width: 170px; height: 170px;
    background: linear-gradient(135deg, #e4e4e6, var(--blue-pale));
    opacity: .7;
  }
  .bands { position: absolute; left: 0; bottom: 0; width: 540px; height: 40px; }
  .details { position: absolute; left: 300px; top: 74px; color: var(--ink); }
  .person-name { font-weight: 900; font-size: 19px; line-height: 1.2; color: var(--blue-deep); }
  .person-title { font-weight: 400; font-size: 14px; color: var(--ink-soft); margin-bottom: 9px; }
  .address { font-size: 14px; line-height: 1.3; margin-bottom: 9px; }
  .contact-list { list-style: none; font-size: 14px; line-height: 1.42; }
  .contact-list li { display: flex; align-items: center; gap: 8px; }
  .contact-list svg { width: 13px; height: 13px; fill: var(--blue-deep); flex: none; }
  .contact-list .web-accent { color: var(--blue-deep); font-weight: 700; }
</style>
</head>
<body>
<main class="stage">

  <section class="card card--contact">
    <div class="watermark" aria-hidden="true"></div>

    <div class="lockup">
      <div class="brand">
        <span class="brand-square"></span>
        <span class="brand-name">Oakridge Interiors</span>
      </div>
      <div class="brand-tagline">Trade Furniture Solutions</div>
    </div>

    <svg class="bands" viewBox="0 0 540 40" aria-hidden="true">
      <defs>
        <linearGradient id="blueBand" x1="0" x2="1" y1="0" y2="0">
          <stop offset="0" stop-color="#85abd2"/>
          <stop offset=".55" stop-color="#3176b5"/>
          <stop offset="1" stop-color="#0555a3"/>
        </linearGradient>
      </defs>
      <path d="M0 24 L240 24 L240 40 L0 40 Z" fill="#1f1d1f"/>
      <path d="M205 24 L240 24 L240 40 L205 40 Z" fill="#6a6a6e"/>
      <path d="M240 40 L240 34 Q240 18 256 18 L540 18 L540 40 Z" fill="url(#blueBand)"/>
    </svg>

    <div class="details">
      <div class="person-name">Daniel Hart</div>
      <div class="person-title">Job Title</div>
      <div class="address">34 Street Name<br>City Name, Country 4567</div>
      <ul class="contact-list">
        <li><svg viewBox="0 0 16 16"><path d="M3 1h3l1 4-2 1a9 9 0 0 0 5 5l1-2 4 1v3a2 2 0 0 1-2 2A13 13 0 0 1 1 3a2 2 0 0 1 2-2z"/></svg><span>000 1234 5678</span></li>
        <li><svg viewBox="0 0 16 16"><path d="M4 0h8a1 1 0 0 1 1 1v14a1 1 0 0 1-1 1H4a1 1 0 0 1-1-1V1a1 1 0 0 1 1-1zm1 2v10h6V2zm3 11a1 1 0 1 0 0 2 1 1 0 0 0 0-2z"/></svg><span>000 1234 5678</span></li>
        <li><svg viewBox="0 0 16 16"><path d="M4 0h8v4H4zM1 5h14v7h-3v4H4v-4H1zm4 5v5h6v-5z"/></svg><span>000 1234 5678</span></li>
        <li><svg viewBox="0 0 16 16"><path d="M0 3h16v10H0zm1 1v.5l7 5 7-5V4zm0 2v6h14V6L8 11z"/></svg><span>info@oakridgeinteriors.com</span></li>
        <li><svg viewBox="0 0 16 16"><path d="M8 0a8 8 0 1 0 0 16A8 8 0 0 0 8 0zm0 1.5c1 0 2 2 2.3 5.5H5.7C6 3.5 7 1.5 8 1.5zM1.6 7h2.6c0-2 .5-3.8 1.2-4.9A6.5 6.5 0 0 0 1.6 7zm10.2 0h2.6a6.5 6.5 0 0 0-3.8-4.9c.7 1.1 1.2 2.9 1.2 4.9zM1.6 9a6.5 6.5 0 0 0 3.8 4.9C4.7 12.8 4.2 11 4.2 9zm4.1 0c.3 3.5 1.3 5.5 2.3 5.5s2-2 2.3-5.5zm6.1 0c0 2-.5 3.8-1.2 4.9A6.5 6.5 0 0 0 14.4 9z"/></svg><span>www.<span class="web-accent">oakridgeinteriors</span>.com</span></li>
      </ul>
    </div>
  </section>

  <section class="card card--logo">
    <div class="brand">
      <span class="brand-square"></span>
      <span class="brand-name">Oakridge Interiors</span>
    </div>
    <div class="brand-tagline">Trade Furniture Solutions</div>
    <div class="site">www.oakridgeinteriors.com</div>
  </section>

</main>
</body>
</html>
```